Home Remodeling company needs a business card design

we need a business card design for home remodeling company in hamilton county, indiana USA. we offers a wide range of construction services including whole house renovations, Design and Build Basements and Kitchen and Bathroom Remodeling . we would like to see designs for both site of business card that use the same color of the company logo and also including all information below :
1- Karim Feltous CEO / General Contractor
2- all company contacts Telephone numbers ( 1-888-DULOM-47 ) ( 317-555-0193) email address ( info@dulomhome.com) website ( www.dulomhome.com ) and social media logos (Facebook- twitter- google plus )
3- company logo
4- licensed . insured . bonded

```html
<!DOCTYPE html>
<html lang="en">
<head>
<meta charset="utf-8">
<title>Dulom Home Remodeling – Business Card</title>
<link rel="stylesheet" href="https://fonts.googleapis.com/css2?family=Lato:wght@400;700;900&display=swap">
<style>
  :root {
    --page: #8d8d8d;
    --card-light: #e9e9eb;
    --card-dark: #2f2f31;
    --ink: #2f2f31;
    --ink-soft: #3d3d40;
    --accent: #b3262c;
    --on-dark: #e8e8ea;
    --rule: #8a8a8c;
  }
  * { margin: 0; padding: 0; box-sizing: border-box; }
  html, body { width: 1105px; height: 1200px; overflow: hidden; }
  body {
    background: var(--page);
    font-family: "Lato", sans-serif;
    position: relative;
  }
  .card {
    position: absolute;
    left: 179px;
    width: 747px;
    height: 427px;
    overflow: hidden;
  }
  .card--front { top: 119px; background: var(--card-light); }
  .card--back  { top: 635px; background: var(--card-dark); }

  /* brand */
  .brand { position: absolute; display: flex; align-items: flex-start; gap: 12px; }
  .brand__square { width: 14px; height: 14px; background: var(--accent); margin-top: 18px; }
  .brand__text { font-weight: 900; line-height: 1; }
  .brand__name { display: block; font-size: 58px; letter-spacing: 2px; }
  .brand__tag { display: block; font-size: 19px; letter-spacing: 6.2px; margin-top: 8px; }
  .card--front .brand { left: 32px; top: 62px; }
  .card--front .brand__text { color: var(--ink); }
  .card--back .brand { left: 186px; top: 176px; }
  .card--back .brand__square { background: var(--on-dark); }
  .card--back .brand__text { color: var(--on-dark); }

  /* name band */
  .name-band { position: absolute; left: 0; top: 186px; width: 747px; height: 67px; }
  .holder { position: absolute; left: 33px; top: 191px; color: #fff; }
  .holder__name { font-size: 26px; font-weight: 700; letter-spacing: 0.3px; line-height: 32px; }
  .holder__role { font-size: 19px; font-weight: 400; line-height: 26px; }

  /* contacts */
  .contacts { position: absolute; left: 34px; top: 277px; list-style: none; }
  .contacts li {
    display: flex; align-items: center; gap: 14px;
    height: 29px; font-size: 19px; color: var(--ink-soft);
  }
  .contacts svg { width: 18px; height: 18px; fill: var(--ink); flex: none; }

  .credentials {
    position: absolute; right: 40px; top: 337px;
    text-align: right; color: var(--accent);
    font-size: 21px; line-height: 29px; letter-spacing: 0.3px;
  }

  /* social row */
  .social { position: absolute; left: 0; top: 360px; width: 747px; height: 28px; }
</style>
</head>
<body>

<section class="card card--front" aria-label="Card front">
  <div class="brand">
    <span class="brand__square"></span>
    <span class="brand__text">
      <span class="brand__name">DULOM</span>
      <span class="brand__tag">HOME REMODELING</span>
    </span>
  </div>

  <svg class="name-band" viewBox="0 0 747 67" aria-hidden="true">
    <rect x="0" y="0" width="13" height="67" fill="var(--accent)"/>
    <polygon points="13,0 747,0 747,25 336,25 311,67 13,67" fill="var(--card-dark)"/>
  </svg>
  <div class="holder">
    <p class="holder__name">Karim Feltous</p>
    <p class="holder__role">CEO / General Contractor</p>
  </div>

  <ul class="contacts">
    <li>
      <svg viewBox="0 0 24 24" aria-hidden="true"><path d="M6.6 10.8a15 15 0 0 0 6.6 6.6l2.2-2.2a1 1 0 0 1 1-.25 11.4 11.4 0 0 0 3.6.57 1 1 0 0 1 1 1V20a1 1 0 0 1-1 1A17 17 0 0 1 3 4a1 1 0 0 1 1-1h3.5a1 1 0 0 1 1 1c0 1.25.2 2.45.57 3.57a1 1 0 0 1-.25 1z"/></svg>
      1-888-DULOM-47
    </li>
    <li>
      <svg viewBox="0 0 24 24" aria-hidden="true"><path d="M7 1h10a2 2 0 0 1 2 2v18a2 2 0 0 1-2 2H7a2 2 0 0 1-2-2V3a2 2 0 0 1 2-2zm0 3v14h10V4zm5 15.2a1.2 1.2 0 1 0 0 2.4 1.2 1.2 0 0 0 0-2.4z"/></svg>
      317-555-0193
    </li>
    <li>
      <svg viewBox="0 0 24 24" aria-hidden="true"><path d="M2 5h20v14H2zm2 2v.4l8 5 8-5V7zm0 2.8V17h16V9.8l-8 5z"/></svg>
      info@dulomhome.com
    </li>
    <li>
      <svg viewBox="0 0 24 24" aria-hidden="true"><circle cx="12" cy="12" r="10"/><path d="M7 8c2 0 3 1 3 2.5S8 12 8 14s2 2 2 4M14 4c0 2 2 2 3 3s-1 3 0 4 3 0 4 1M13 20c0-2 1-3 3-3" stroke="var(--card-light)" stroke-width="1.6" fill="none"/></svg>
      www.dulomhome.com
    </li>
  </ul>

  <p class="credentials">LICENSED<br>INSURED | BONDED</p>
</section>

<section class="card card--back" aria-label="Card back">
  <div class="brand">
    <span class="brand__square"></span>
    <span class="brand__text">
      <span class="brand__name">DULOM</span>
      <span class="brand__tag">HOME REMODELING</span>
    </span>
  </div>

  <svg class="social" viewBox="0 0 747 28" role="img" aria-label="Social media links">
    <line x1="270" y1="14" x2="326" y2="14" stroke="var(--rule)" stroke-width="1.2"/>
    <line x1="421" y1="14" x2="477" y2="14" stroke="var(--rule)" stroke-width="1.2"/>
    <circle cx="342" cy="14" r="12" fill="var(--on-dark)"/>
    <circle cx="373" cy="14" r="12" fill="var(--on-dark)"/>
    <circle cx="405" cy="14" r="12" fill="var(--on-dark)"/>
  </svg>
</section>

</body>
</html>
```